Corvana Tongue Works, LLC

We need a business card that includes information about our business and conveys a reliable business that provides document translation services and interpreters for a variety of corporate and individual clients. We want to come across as professional, reliable, yet approachable. It should include the following on one side:

ESL / ENL Language Classes, Private Lessons, and Online Tutors
PLEXA Training and Testing
Translating & Interpreting Services
Contact us about Over-the-Phone Interpreting in over 200 languages
24/7/365
www.corvanatongue.example

The other side should include (555) 481-3062

Rhoda Pelling, President
482 Garnet Ave., Ste. 219
Indianapolis, IN 40917

Please add USA as part of the address. Also, please add rmpelling@corvanatongueworks.example as the e-mail address. Thank you.

Target Market(s)

Business professionals, their families, the international community

Industry/Entity Type

Business

Contact Information for Business Card

24/7/365
www.corvanatongue.example

(555) 481-3062

Rhoda Pelling, President
482 Garnet Ave., Ste. 219
Indianapolis, IN 40917
USA

Font styles to use
Sans Serif

Colors

Designer to choose colors to be used in the design.

Requirements
Must have
• See project description
• e-mail address and web address
• Phone number
Nice to have
• a globe
• physical address
Should not have
• Should not have the same color scheme as other agencies in our market in Indiana unless it is blue and black. No purple or yellow.

```html
<!DOCTYPE html>
<html lang="en">
<head>
<meta charset="utf-8">
<title>Corvana Tongue Works – Business Card</title>
<link href="https://fonts.googleapis.com/css2?family=Lato:wght@400;700;900&display=swap" rel="stylesheet">
<style>
  :root {
    --backdrop: #262626;
    --card-white: #f4f4f3;
    --brand-blue: #2394d3;
    --brand-blue-light: #3ba4dc;
    --ink: #1d1d1d;
    --ink-soft: #4a4a4a;
    --white: #ffffff;
  }
  * { margin: 0; padding: 0; box-sizing: border-box; }
  html, body {
    width: 1200px; height: 960px; overflow: hidden;
    background: var(--backdrop);
    font-family: "Lato", sans-serif;
  }
  .stage { position: relative; width: 1200px; height: 960px; }
  .card {
    position: absolute; width: 600px; height: 343px;
    border-radius: 18px; overflow: hidden;
  }
  .card--front { left: 302px; top: 129px; background: var(--card-white); }
  .card--back { left: 299px; top: 488px; background: var(--brand-blue); }

  .name-band { position: absolute; left: 0; top: 44px; }
  .holder { position: absolute; left: 50px; top: 74px; color: var(--white); }
  .holder__name { font-size: 20px; font-weight: 900; letter-spacing: 0.2px; line-height: 22px; }
  .holder__title { font-size: 15px; font-weight: 900; margin-left: 2px; line-height: 20px; }

  .brand-mark { position: absolute; left: 324px; top: 42px; }
  .brand-name {
    position: absolute; left: 426px; top: 48px;
    font-size: 25px; font-weight: 400; line-height: 28px; color: var(--ink);
  }

  .contact { position: absolute; top: 238px; font-size: 15px; line-height: 19px; color: var(--ink-soft); }
  .contact--left { left: 52px; }
  .contact--left li { list-style: none; display: flex; align-items: center; gap: 7px; white-space: nowrap; }
  .contact--left svg { width: 14px; height: 14px; flex: none; }
  .contact--right { right: 51px; text-align: right; font-style: normal; white-space: nowrap; }

  .map-field { position: absolute; left: 0; top: 0; width: 600px; height: 343px; }
  .services {
    position: absolute; left: 0; right: 0; top: 79px;
    text-align: center; color: var(--white);
  }
  .services__list { font-size: 16px; line-height: 19px; list-style: none; }
  .services__call { margin-top: 18px; font-size: 18px; font-weight: 700; line-height: 21px; text-transform: uppercase; }
  .services__hours { margin-top: 20px; font-size: 20px; font-weight: 900; display: flex; justify-content: center; align-items: center; gap: 6px; }
  .services__hours svg { width: 19px; height: 19px; }
  .services__web { margin-top: 4px; font-size: 17px; }
  .services__web strong { font-weight: 900; }
</style>
</head>
<body>
<main class="stage">

  <section class="card card--front" aria-label="Card front">
    <svg class="name-band" width="360" height="93" viewBox="0 0 360 93" aria-hidden="true">
      <polygon points="0,0 360,0 335,93 0,93" fill="var(--brand-blue)"/>
    </svg>
    <div class="holder">
      <p class="holder__name">RHODA PELLING</p>
      <p class="holder__title">PRESIDENT</p>
    </div>
    <svg class="brand-mark" width="98" height="98" viewBox="0 0 98 98" aria-hidden="true">
      <circle cx="49" cy="49" r="48" fill="var(--white)"/>
      <circle cx="49" cy="49" r="46" fill="none" stroke="var(--brand-blue)" stroke-width="2"/>
      <circle cx="49" cy="49" r="40" fill="var(--brand-blue)"/>
    </svg>
    <p class="brand-name">Corvana<br>Tongue<br>Works, LLC</p>

    <ul class="contact contact--left">
      <li>
        <svg viewBox="0 0 14 14"><path d="M3 1l2.5 3-1.3 1.6a7 7 0 0 0 4.2 4.2L10 8.5 13 11l-1.2 2A10 10 0 0 1 1 2.2z" fill="var(--brand-blue)"/></svg>
        (555) 481-3062
      </li>
      <li>
        <svg viewBox="0 0 14 14"><rect x="1" y="3" width="12" height="8.5" rx="1" fill="var(--brand-blue)"/><path d="M1.5 3.5L7 8l5.5-4.5" fill="none" stroke="var(--card-white)" stroke-width="1.1"/></svg>
        rmpelling@corvanatongueworks.example
      </li>
      <li>
        <svg viewBox="0 0 14 14"><circle cx="7" cy="7" r="6" fill="var(--brand-blue)"/><path d="M4 5.5l2 .5 1 2-1.5 2.5M9 3.5l.5 2 2 1" fill="none" stroke="var(--card-white)" stroke-width="1.1"/></svg>
        www.corvanatongue.example
      </li>
    </ul>
    <address class="contact contact--right">
      482 Garnet Ave., Ste. 219<br>Indianapolis, IN 40917<br>USA
    </address>
  </section>

  <section class="card card--back" aria-label="Card back">
    <svg class="map-field" role="img" aria-label="Faint world map spread across the card background" viewBox="0 0 600 343">
      <defs>
        <radialGradient id="mapGlow" cx="50%" cy="50%" r="60%">
          <stop offset="0" stop-color="var(--brand-blue-light)"/>
          <stop offset="1" stop-color="var(--brand-blue)"/>
        </radialGradient>
      </defs>
      <rect width="600" height="343" fill="url(#mapGlow)"/>
    </svg>
    <div class="services">
      <ul class="services__list">
        <li>ESL / ENL Language Classes, Private Lessons, &amp; Online Tutors</li>
        <li>PLEXA Training &amp; Testing</li>
        <li>Translating &amp; Interpreting Services</li>
      </ul>
      <p class="services__call">Contact us about over-the-phone<br>interpreting in over 200 languages</p>
      <p class="services__hours">
        <svg viewBox="0 0 20 20" aria-hidden="true"><circle cx="10" cy="10" r="8.5" fill="none" stroke="var(--white)" stroke-width="1.6"/><path d="M10 10L7 15" stroke="var(--white)" stroke-width="1.6" stroke-linecap="round"/></svg>
        24/7/365
      </p>
      <p class="services__web">www.<strong>CORVANATONGUE</strong>.example</p>
    </div>
  </section>

</main>
</body>
</html>
```